Business Card for Vorla Parts Wholesale supplier

Hi There! I need a new business card for our company. We are specialized in selling Vorla parts, mostly we sell new LCD screens for Zelnar and Drelks. I would like to see that back in the design.

You can find the colors and logo's on our website: www.hartuvo.nl

Industry/Entity Type

Business

Contact Information for Business Card

My Details:
Tobias Lindqvist

Phone: 0031687203316
E-mail: Tobias@hartuvo.nl

Slogan: "Built To Keep Running"

Font styles to use
Sans Serif

Colors

Designer to choose colors to be used in the design.

Requirements
Must have
• A Black backside with the Hartuvo logo on it. The front side should be clean with only my contact details.
• But I'm also open for something really different or awesome!
Nice to have
• Remember that we are in the parts & repairing industry, So i'll be handing those business cards mainly to repair companies. Maybe you can do something with that thought :)

```html
<!DOCTYPE html>
<html lang="en">
<head>
<meta charset="UTF-8">
<title>Hartuvo Business Card</title>
<link rel="stylesheet" href="https://fonts.googleapis.com/css2?family=Open+Sans:wght@400;600;700;800&display=swap">
<style>
  :root {
    --stage: #2e2a28;
    --ink: #111111;
    --orange: #ec6b22;
    --orange-soft: #fdf0e7;
    --paper: #ffffff;
    --back-dark: #0c0908;
  }
  * { box-sizing: border-box; margin: 0; padding: 0; }
  html, body { width: 1200px; height: 780px; overflow: hidden; }
  body {
    background: var(--stage);
    font-family: "Open Sans", Arial, sans-serif;
    position: relative;
  }
  .card {
    position: absolute;
    width: 520px;
    height: 300px;
    overflow: hidden;
    box-shadow: 0 14px 30px rgba(0,0,0,0.45);
  }
  .card--back {
    left: 50px; top: 130px;
    background: linear-gradient(200deg, var(--orange) 0%, #9a4a1f 38%, #3a2216 62%, var(--back-dark) 100%);
    display: flex; align-items: center; justify-content: center;
  }
  .card--front {
    left: 630px; top: 350px;
    background: var(--paper);
  }
  .brand {
    display: flex; align-items: center; gap: 14px;
    font-family: "Open Sans", Arial, sans-serif;
    font-weight: 800;
    letter-spacing: 1px;
    line-height: 1;
  }
  .brand__mark { display: block; border-radius: 50%; flex: none; }
  .card--back .brand { color: #ffffff; font-size: 62px; }
  .card--back .brand__mark { width: 46px; height: 46px; background: #ffffff; }
  .card--front .brand {
    position: absolute; left: 28px; top: 28px;
    color: var(--ink); font-size: 50px;
  }
  .card--front .brand__mark { width: 38px; height: 38px; background: var(--orange); }
  .backdrop-disc {
    position: absolute; right: -40px; top: 110px;
    width: 260px; height: 260px; border-radius: 50%;
    background: var(--orange-soft);
  }
  .contact {
    position: absolute; left: 30px; top: 150px;
    font-size: 14px; line-height: 1.35; color: var(--ink);
  }
  .contact__name {
    color: var(--orange); font-weight: 700; font-size: 19px; margin-bottom: 8px;
  }
  .contact__label { color: var(--orange); font-weight: 700; }
  .contact__site-accent { color: var(--orange); }
  .slogan {
    position: absolute; right: 24px; bottom: 20px;
    font-weight: 700; font-size: 14px; color: var(--ink);
  }
</style>
</head>
<body>
  <section class="card card--back" aria-label="Card back">
    <div class="brand"><span class="brand__mark"></span><span class="brand__name">hartuvo</span></div>
  </section>

  <section class="card card--front" aria-label="Card front">
    <div class="backdrop-disc"></div>
    <div class="brand"><span class="brand__mark"></span><span class="brand__name">hartuvo</span></div>
    <div class="contact">
      <p class="contact__name">Tobias Lindqvist</p>
      <p><span class="contact__label">P:</span> 0031687203316</p>
      <p><span class="contact__label">E:</span> Tobias@hartuvo.nl</p>
      <p>www.<span class="contact__site-accent">hartuvo</span>.nl</p>
    </div>
    <p class="slogan">Built To Keep Running</p>
  </section>
</body>
</html>
```